Brightfern Care Alliance Flirvo Ads

We want an ad created for the gay dating app flirvo. The size is 300x250. We want the ad to be sexy, with a shirtless man. We are advertising our free HIV and PrEP services. We are open to slogans about maybe "Bringing HIV and PrEP To You"
"Free PrEP and HIV Management"
Open to ideas.

We also offer through the Cedarline Relief Fund
Copay Assistance, Insurance Premium Assistance, Free Medical Services, etc
Our website is bfcanj.org

I do want the ad to have a Book Now Button

Gay sexually active males

```html
<!DOCTYPE html>
<html lang="en">
<head>
<meta charset="utf-8">
<title>Brightfern Care Alliance – Free PrEP &amp; HIV Management</title>
<link href="https://fonts.googleapis.com/css2?family=Montserrat:wght@400;600;700;800&display=swap" rel="stylesheet">
<style>
  :root {
    --page-bg: #9a9a9a;
    --ad-bg: #2a2a2a;
    --ad-band: #232323;
    --ink-white: #f4f4f4;
    --accent-orange: #ff6a1a;
    --grad-blue: #0f82ff;
    --grad-violet: #8b2fe6;
    --grad-pink: #ff45d8;
    --grad-orange: #ff6b2c;
    --brand-dot: #8b3fe0;
  }
  html, body {
    margin: 0;
    width: 1200px;
    height: 1200px;
    overflow: hidden;
    background: var(--page-bg);
  }
  .stage {
    position: relative;
    width: 1200px;
    height: 1200px;
  }
  .ad {
    position: absolute;
    left: 20px;
    top: 99px;
    width: 1397px;
    height: 1207px;
    transform: scale(0.8303);
    transform-origin: 0 0;
    background: var(--ad-bg);
    overflow: hidden;
    font-family: "Montserrat", Arial, sans-serif;
  }
  .ad__top-band {
    position: absolute;
    left: 0; top: 0;
    width: 100%; height: 50px;
    background: var(--ad-band);
  }
  .ad__photo {
    position: absolute;
    left: 812px; top: 80px;
    width: 585px; height: 1127px;
    background:
      linear-gradient(100deg, rgba(255,120,40,0.55) 0%, rgba(240,200,170,0.35) 35%, rgba(90,220,230,0.45) 55%, rgba(140,60,230,0.6) 72%, rgba(40,30,40,0.2) 100%);
  }
  .ad__arc {
    position: absolute;
    left: 0; top: 0;
    width: 1397px; height: 1207px;
  }
  .brand {
    position: absolute;
    left: 60px; top: 180px;
    display: flex;
    align-items: center;
    gap: 22px;
  }
  .brand__dot {
    width: 118px; height: 118px;
    border-radius: 50%;
    background: var(--brand-dot);
  }
  .brand__name {
    color: var(--ink-white);
    font-weight: 700;
    font-size: 44px;
    line-height: 1.1;
    letter-spacing: 1px;
  }
  .tagline {
    position: absolute;
    left: 44px; top: 362px;
    margin: 0;
    color: var(--ink-white);
    font-weight: 400;
    font-size: 36px;
  }
  .tagline__you {
    color: var(--accent-orange);
    font-weight: 800;
  }
  .headline {
    position: absolute;
    left: 40px; top: 410px;
    width: 860px;
    margin: 0;
    font-weight: 800;
    background: linear-gradient(105deg, var(--grad-blue) 0%, var(--grad-blue) 18%, var(--grad-violet) 40%, var(--grad-pink) 62%, var(--grad-orange) 85%);
    -webkit-background-clip: text;
    background-clip: text;
    color: transparent;
  }
  .headline__line { display: block; }
  .headline__line--free, .headline__line--services {
    font-size: 136px;
    line-height: 116px;
    letter-spacing: -1px;
  }
  .headline__line--management {
    font-size: 110px;
    line-height: 114px;
    letter-spacing: -1px;
  }
  .cta {
    position: absolute;
    left: 171px; top: 805px;
    width: 431px; height: 77px;
    display: flex;
    align-items: center;
    justify-content: center;
    background: linear-gradient(90deg, #4f7cff 0%, #b45cf0 55%, #ff4fa8 100%);
    color: #fff;
    font-weight: 700;
    font-size: 27px;
    letter-spacing: 7px;
    text-decoration: none;
  }
</style>
</head>
<body>
<div class="stage">
  <section class="ad">
    <div class="ad__top-band"></div>

    <svg class="ad__arc" viewBox="0 0 1397 1207" aria-hidden="true">
      <defs>
        <linearGradient id="arcGradient" x1="0" y1="0" x2="1" y2="0">
          <stop offset="0" stop-color="#b13be8"/>
          <stop offset="0.35" stop-color="#ff45d8"/>
          <stop offset="0.65" stop-color="#ff4a7a"/>
          <stop offset="1" stop-color="#ff7a2c"/>
        </linearGradient>
      </defs>
      <circle cx="677" cy="2002" r="1030" fill="#000" stroke="url(#arcGradient)" stroke-width="34"/>
    </svg>

    <div class="ad__photo" role="img" aria-label="Two raised hands, one holding the other's wrist, lit by a rainbow of orange, teal and purple light"></div>

    <div class="brand">
      <span class="brand__dot"></span>
      <span class="brand__name">Brightfern<br>Care Alliance</span>
    </div>

    <p class="tagline">Bringing HIV and PrEP To <span class="tagline__you">YOU!</span></p>

    <h1 class="headline">
      <span class="headline__line headline__line--free">FREE</span>
      <span class="headline__line headline__line--services">PrEP &amp; HIV</span>
      <span class="headline__line headline__line--management">MANAGEMENT</span>
    </h1>

    <a class="cta" href="#">BOOK NOW</a>
  </section>
</div>
</body>
</html>
```